Business Cards - Brightpath Horizon

need to design unique business card for my mortgage business. I need to design credit card style business card for my business or any unique idea that you might have

Target Market(s)

Home Loan customers

Industry/Entity Type

Mortgage Brokerage

Contact Information for Business Card

please design credit card style or very unique style business card

Colors

Designer to choose colors to be used in the design.

Requirements
Must have
• Name
• position
• Phone number
• fax number
• email address
• website address
• social media address
• All above fields will be provided once design in finalised

```html
<!DOCTYPE html>
<html lang="en">
<head>
<meta charset="utf-8">
<title>Brightpath Horizon – Business Card</title>
<link href="https://fonts.googleapis.com/css2?family=Tinos:wght@400;700&display=swap" rel="stylesheet">
<style>
  :root{
    --backdrop:#262626;
    --card-white:#ffffff;
    --card-shade:#d4d4d4;
    --brand-blue:#0a2fc0;
    --brand-blue-light:#7f93e2;
    --accent-orange:#f7921e;
    --text-grey:#4a4a4a;
    --white:#ffffff;
  }
  *{margin:0;padding:0;box-sizing:border-box}
  html,body{width:1200px;height:960px;overflow:hidden}
  body{background:var(--backdrop);position:relative;font-family:"Tinos",serif}

  .card{position:absolute;width:600px;height:343px;border-radius:20px;overflow:hidden}
  .card--front{left:314px;top:113px;
    background:linear-gradient(135deg,var(--card-white) 0%,var(--card-white) 55%,var(--card-shade) 100%)}
  .card--back{left:311px;top:472px;
    background:linear-gradient(120deg,var(--brand-blue-light) 0%,#3f5bd6 25%,var(--brand-blue) 55%,var(--brand-blue) 100%)}

  .brand{display:flex;align-items:center;gap:12px;position:absolute}
  .brand__mark{width:30px;height:30px;flex:none}
  .brand__name{font-family:"Tinos",serif;font-weight:700;font-size:31px;line-height:1;letter-spacing:.5px;white-space:nowrap}

  .card--front .brand{left:54px;top:84px}
  .card--front .brand__mark{background:var(--accent-orange)}
  .card--front .brand__name{color:var(--brand-blue)}

  .person{position:absolute;left:55px;top:244px}
  .person__name{font-weight:700;font-size:21px;color:var(--brand-blue);letter-spacing:.3px}
  .person__role{font-size:15px;color:var(--accent-orange);margin-top:3px;letter-spacing:.3px}

  .contact{position:absolute;left:380px;top:229px;list-style:none}
  .contact__item{display:flex;align-items:center;gap:8px;height:19.5px;font-size:14.5px;color:var(--text-grey)}
  .contact__icon{width:13px;height:13px;flex:none;fill:var(--brand-blue)}

  .card--back .brand{left:50%;top:118px;transform:translateX(-50%)}
  .card--back .brand__mark{border-radius:50%;background:var(--white)}
  .card--back .brand__name{color:var(--white);font-size:34px}

  .social{position:absolute;left:50%;top:280px;transform:translateX(-50%);display:flex;gap:3px;list-style:none}
  .social__dot{width:27px;height:27px;border-radius:50%;background:var(--white)}
</style>
</head>
<body>

<section class="card card--front">
  <div class="brand">
    <span class="brand__mark"></span>
    <span class="brand__name">Brightpath Horizon</span>
  </div>

  <div class="person">
    <p class="person__name">DANIEL REEVE</p>
    <p class="person__role">CEO/FOUNDER</p>
  </div>

  <ul class="contact">
    <li class="contact__item">
      <svg class="contact__icon" viewBox="0 0 16 16" aria-hidden="true"><path d="M3.5 1l3 3-1.6 2c.9 1.9 2.4 3.4 4.3 4.3l2-1.6 3 3-1.8 2.3C7 13.5 2.5 9 1.2 2.8z"/></svg>
      <span>555 214 7386</span>
    </li>
    <li class="contact__item">
      <svg class="contact__icon" viewBox="0 0 16 16" aria-hidden="true"><path d="M4 1h8v4H4zM1 6h14v6h-3v3H4v-3H1zm4 4v3h6v-3z"/></svg>
      <span>555 730 1194</span>
    </li>
    <li class="contact__item">
      <svg class="contact__icon" viewBox="0 0 16 16" aria-hidden="true"><path d="M1 3h14v10H1zm1.5 1.5v.4L8 9l5.5-4.1v-.4z"/></svg>
      <span>mail@brightpath.com</span>
    </li>
    <li class="contact__item">
      <svg class="contact__icon" viewBox="0 0 16 16" aria-hidden="true"><circle cx="8" cy="8" r="7"/><path d="M4 5c2 0 2 2 4 2s1 3 3 3M9 2c0 2 2 2 3 3" stroke="#fff" stroke-width="1.3" fill="none"/></svg>
      <span>www.brightpath.com</span>
    </li>
  </ul>
</section>

<section class="card card--back">
  <div class="brand">
    <span class="brand__mark"></span>
    <span class="brand__name">Brightpath Horizon</span>
  </div>
  <ul class="social" aria-label="Social media">
    <li class="social__dot"></li>
    <li class="social__dot"></li>
    <li class="social__dot"></li>
    <li class="social__dot"></li>
  </ul>
</section>

</body>
</html>
```